Income Tax and Accounting Brochure

I need a brochure using my new logo (file attached). I do tax work and accounting work. I am an EA (QFB Enrolled Agent - logo attached) and would like this incorporated into the brochure. I also have a MSA in Accounting. Please incorporate the text that I have provided in the brochure.
Updates

Need extra days to review

Target Market(s)

Tax Clients - both business and individuals

Industry/Entity Type

Accounting

Colors
0054AA
0677BA
7BADD7
CADEEF
E8F1F8

Requirements
Must have
• Use my logo and the QFB EA file in the brochure
Nice to have
• I would like to see a brochure that I can customize with my own text if possible.

```html
<!DOCTYPE html>
<html lang="en">
<head>
<meta charset="utf-8">
<title>LMR Accounting &amp; Consulting – Brochure</title>
<link href="https://fonts.googleapis.com/css2?family=Crimson+Text:ital,wght@0,400;1,400&family=Poppins:ital,wght@0,400;0,500;1,400&display=swap" rel="stylesheet">
<style>
  :root{
    --backdrop:#c9c9c9;
    --paper:#f1f1f1;
    --blue-deep:#2f66ad;
    --blue-mid:#3a79bd;
    --blue-bright:#2e8fca;
    --blue-navy:#2a4f9a;
    --red:#c0434d;
    --red-soft:#cd5a62;
    --ink:#3a3a3a;
    --heading-blue:#2f6fb4;
    --accent-red:#c5343f;
    --badge-grey:#cfcfcf;
  }
  *{box-sizing:border-box;margin:0;padding:0}
  html,body{width:1200px;height:800px;overflow:hidden;background:var(--backdrop)}
  .canvas{position:relative;width:1200px;height:800px}
  .page{position:absolute;top:30px;width:540px;height:740px;background:var(--paper);overflow:hidden;box-shadow:0 6px 24px rgba(0,0,0,.18)}
  .page--left{left:60px}
  .page--right{left:600px}
  .page__art{position:absolute;inset:0;width:100%;height:100%}
  .page__content{position:absolute;font-family:"Poppins",sans-serif;color:var(--ink)}

  /* left page */
  .brand{position:absolute;left:150px;top:110px;display:flex;align-items:center;gap:14px}
  .brand__mark{width:56px;height:56px;border-radius:50%;background:var(--blue-deep)}
  .brand__name{font-family:"Poppins",sans-serif;font-weight:500;color:var(--blue-deep);font-size:17px;line-height:1.25;letter-spacing:1.5px;text-transform:uppercase}
  .about{left:52px;top:200px;width:440px}
  .about__title{font-family:"Crimson Text",serif;font-weight:400;color:var(--heading-blue);font-size:25px;line-height:1.2;margin-bottom:14px}
  .about p{font-size:11.5px;line-height:1.55;margin-bottom:10px}
  .credential-badge{margin:16px 0 0 28px;width:230px;height:72px;background:#f6f6f6;border:1px solid var(--badge-grey);display:flex;align-items:center;gap:14px;padding:0 12px}
  .credential-badge__frame{width:70px;height:48px;border:4px solid var(--badge-grey)}
  .credential-badge__bar{flex:1;height:36px;background:var(--badge-grey)}

  /* right page */
  .services{left:40px;top:82px;width:460px}
  .services__title{font-family:"Crimson Text",serif;font-style:italic;font-weight:400;color:var(--heading-blue);font-size:26px;line-height:1.2;margin-bottom:8px}
  .services__sub{font-family:"Crimson Text",serif;font-style:italic;color:var(--accent-red);font-size:15px;margin:10px 0 4px}
  .services p,.services li{font-style:italic;font-size:11px;line-height:1.5}
  .benefits{list-style:none}
  .benefits li{position:relative;padding-left:12px;margin-bottom:9px}
  .benefits li::before{content:"·";position:absolute;left:0;top:0}
</style>
</head>
<body>
<div class="canvas">

  <section class="page page--left">
    <svg class="page__art" viewBox="0 0 540 740" aria-hidden="true">
      <path d="M300 0 C400 20 470 80 540 170 L540 0 Z" fill="var(--red-soft)"/>
      <path d="M330 0 C420 40 480 110 540 210 L540 150 C480 70 420 20 370 0 Z" fill="var(--blue-bright)"/>
      <path d="M360 0 C440 40 500 110 540 190 L540 230 C490 120 420 40 330 0 Z" fill="var(--blue-navy)"/>
      <path d="M0 580 L540 690 L540 740 L0 740 Z" fill="#d3d3d3" opacity=".7"/>
      <path d="M120 540 L540 640 L540 740 L260 740 Z" fill="#dadada" opacity=".8"/>
      <path d="M220 600 L540 600 L540 740 Z" fill="#c9c9c9" opacity=".6"/>
      <path d="M0 500 C40 600 140 690 300 740 L0 740 Z" fill="var(--blue-bright)"/>
      <path d="M0 530 C50 620 150 700 290 740 L0 740 Z" fill="var(--red)"/>
      <path d="M0 560 C60 640 160 710 270 740 L0 740 Z" fill="var(--blue-mid)"/>
      <path d="M0 590 C80 670 170 720 240 740 L0 740 Z" fill="var(--blue-deep)"/>
    </svg>

    <div class="brand">
      <span class="brand__mark"></span>
      <span class="brand__name">LMR Accounting &amp;<br>Consulting, LLC</span>
    </div>

    <div class="page__content about">
      <h1 class="about__title">About Marian T Holloway, MSA EA “Principal”</h1>
      <p>I have a Masters’ Degree in accounting and am an QFB Enrolled Agent. I am also a Ledgerly Advanced Certified Consultant in both the online and desktop products including Enterprise and Point of Sale. I provide individual and small business tax services, Accounting, bookkeeping, QFB representation, insurance audit representation, business license assistance and more.</p>
      <p>I have experience working with a wide variety of clients from the point where they first decide they want to start a business. They are often unsure about what to do first- I have a lot of experience to offer you.</p>
      <div class="credential-badge" role="img" aria-label="Enrolled agent credential badge">
        <span class="credential-badge__frame"></span>
        <span class="credential-badge__bar"></span>
      </div>
    </div>
  </section>

  <section class="page page--right">
    <svg class="page__art" viewBox="0 0 540 740" aria-hidden="true">
      <path d="M0 0 L540 0 L540 70 C400 20 200 10 0 60 Z" fill="var(--red)"/>
      <path d="M0 0 L540 0 L540 40 C380 0 200 0 0 30 Z" fill="var(--red-soft)" opacity=".6"/>
      <path d="M0 700 C150 690 350 680 540 640 L540 740 L0 740 Z" fill="var(--red)"/>
      <path d="M200 740 L540 660 L540 740 Z" fill="var(--red-soft)" opacity=".6"/>
    </svg>

    <div class="page__content services">
      <h2 class="services__title">What a joy it is to watch success in action!</h2>
      <h3 class="services__sub">Tax Preparation – why hire us?</h3>
      <p>Preparing your own income tax return can be a task that leaves you with more questions than answers. According to a study released by the National Audit Bureau last year, most taxpayers (77% of 71 million taxpayers) believe they benefited from using a professional tax preparer. Whether we like it or not, today’s tax laws are so complicated that filing a relatively simple return can be confusing. It is just too easy to overlook deductions and credits to which you are entitled. Even if you use a computer software program there’s no substitute for the assistance of an experienced tax professional.</p>

      <h3 class="services__sub">Here’s what your get...</h3>
      <ul class="benefits">
        <li>Your tax return will be checked and rechecked by our computer software identifying potential problems the QFB may look at more closely and reviewing the math to limit QFB contacts.</li>
        <li>Your tax return can be filed electronically so you will get a refund back quicker.</li>
        <li>Our staff will show you how to adjust your payroll withholding to get more money back each week. Why give the QFB an interest free loan for up to 16 months.</li>
        <li>We will show you potential deductions to limit your tax liability for next year. In addition, we will give you a sheet of commonly overlooked deductions to limit the following year’s tax liability.</li>
      </ul>

      <h3 class="services__sub">Books a Mess: No Problem!</h3>
      <p>If you own a small business and haven’t kept up your bookkeeping, don’t worry. We can help you. We’ll prepare your bookkeeping for the year, prepare a full Schedule C, as well as your personal income tax return. Then we’ll help you set up an easy system that allows you to keep your books in tip-top shape next year.</p>
    </div>
  </section>

</div>
</body>
</html>
```